Medical Billing Company Needs a Business Card Design

We need a business card design for a Florida based medical billing company called 'Clinicians Keystone Solutions'. We specialize in providing revenue cycle management services to physician and therapist offices (we're basically their back-office processing partner for providing billing software, claims submissions, A/R follow-up and patient statements & collections. Our logo is red and blue-ish, so make sure that whatever other elements are used will match appropriately. Our current business card design has a too small font size. I'd like to project an image that shows we are modern & reliable. On a side note, I'm planning on using ZUB for printing these cards.

Target Market(s)

Office managers, physicians, therapists

Industry/Entity Type

Printing

Requirements
Must have
• Logo
Name of Employee
Phone
Fax
E-mail
Website

```html
<!DOCTYPE html>
<html lang="en">
<head>
<meta charset="utf-8">
<title>Clinicians Keystone Solutions – Business Card</title>
<link rel="stylesheet" href="https://fonts.googleapis.com/css2?family=Cabin:wght@400;500&display=swap">
<style>
  :root {
    --navy: #2b2a78;
    --red: #b3242c;
    --ink: #3c3c46;
    --white: #ffffff;
    --silver-light: #f4f4f6;
    --silver-mid: #dcdde1;
    --silver-dark: #c9cace;
    --backdrop: #ecebe8;
  }
  * { box-sizing: border-box; margin: 0; padding: 0; }
  html, body { width: 1200px; height: 720px; overflow: hidden; }
  body {
    background: var(--backdrop);
    font-family: "Cabin", sans-serif;
    position: relative;
  }
  .card {
    position: absolute;
    top: 206px;
    width: 540px;
    height: 308px;
    border-radius: 4px;
    overflow: hidden;
    background:
      repeating-linear-gradient(0deg, rgba(255,255,255,0.25) 0 1px, rgba(0,0,0,0.02) 1px 3px),
      linear-gradient(160deg, var(--silver-light) 0%, var(--silver-mid) 55%, var(--silver-dark) 100%);
    box-shadow: 0 3px 0 #b9babe, 0 6px 0 #a9aaae, 0 14px 24px rgba(0,0,0,0.18);
  }
  .card--front { left: 40px; }
  .card--back { left: 620px; }

  .brand {
    display: flex;
    align-items: center;
    gap: 12px;
    white-space: nowrap;
  }
  .brand-name {
    color: var(--navy);
    font-weight: 400;
    letter-spacing: 2px;
    text-transform: uppercase;
  }
  .brand-square {
    width: 14px;
    height: 14px;
    background: var(--red);
    flex: none;
  }
  .card--front .brand {
    position: absolute;
    left: 30px;
    top: 34px;
  }
  .card--front .brand-name { font-size: 27px; }

  .holder {
    position: absolute;
    left: 34px;
    top: 110px;
    font-size: 19px;
    color: var(--navy);
  }
  .holder .title { color: var(--red); font-size: 16px; }

  .contact-list {
    position: absolute;
    left: 34px;
    top: 144px;
    list-style: none;
    font-size: 13.5px;
    color: var(--ink);
    line-height: 21px;
  }
  .contact-list li { display: flex; align-items: center; gap: 7px; }
  .contact-list svg { width: 12px; height: 12px; fill: var(--ink); flex: none; }

  .address {
    position: absolute;
    left: 34px;
    top: 216px;
    font-size: 13px;
    color: var(--ink);
    line-height: 16px;
    font-style: normal;
  }

  .band {
    position: absolute;
    left: 0;
    bottom: 0;
    width: 540px;
    height: 64px;
  }
  .band-url {
    font-family: "Cabin", sans-serif;
    font-size: 12px;
    fill: var(--white);
    letter-spacing: 0.2px;
  }

  .card--back .brand {
    position: absolute;
    left: 0;
    right: 0;
    top: 124px;
    justify-content: center;
  }
  .card--back .brand-name { font-size: 30px; }
  .card--back .web {
    position: absolute;
    left: 0;
    right: 0;
    top: 180px;
    text-align: center;
    font-size: 16px;
    letter-spacing: 0.8px;
    color: var(--ink);
  }
</style>
</head>
<body>

  <section class="card card--front" aria-label="Business card front">
    <div class="brand">
      <span class="brand-name">Clinicians Keystone</span>
      <span class="brand-square" aria-hidden="true"></span>
    </div>

    <p class="holder">Your Name, <span class="title">Title</span></p>

    <ul class="contact-list">
      <li>
        <svg viewBox="0 0 24 24" aria-hidden="true"><path d="M6.6 10.8a15.1 15.1 0 0 0 6.6 6.6l2.2-2.2c.3-.3.7-.4 1-.2 1.1.4 2.3.6 3.6.6.6 0 1 .4 1 1V20c0 .6-.4 1-1 1C10.6 21 3 13.4 3 4c0-.6.4-1 1-1h3.5c.6 0 1 .4 1 1 0 1.3.2 2.5.6 3.6.1.3 0 .7-.2 1z"/></svg>
        123-456-0789
      </li>
      <li>
        <svg viewBox="0 0 24 24" aria-hidden="true"><path d="M7 2h10a1 1 0 0 1 1 1v18a1 1 0 0 1-1 1H7a1 1 0 0 1-1-1V3a1 1 0 0 1 1-1zm1 3v12h8V5zm4 13.5a1 1 0 1 0 0 2 1 1 0 0 0 0-2z"/></svg>
        123-456-0789
      </li>
      <li>
        <svg viewBox="0 0 24 24" aria-hidden="true"><path d="M3 5h18a1 1 0 0 1 1 1v12a1 1 0 0 1-1 1H3a1 1 0 0 1-1-1V6a1 1 0 0 1 1-1zm1 2.3V17h16V7.3l-8 5.2z"/></svg>
        info@cliniciankeystone.com
      </li>
    </ul>

    <address class="address">Street Name, City Name<br>State Zip Code</address>

    <svg class="band" viewBox="0 0 540 64" aria-label="www.cliniciankeystone.com">
      <polygon points="0,42 348,42 334,64 0,64" fill="var(--red)"/>
      <polygon points="374,14 540,14 540,42 356,42" fill="var(--navy)"/>
      <text class="band-url" x="532" y="32" text-anchor="end">www.cliniciankeystone.com</text>
    </svg>
  </section>

  <section class="card card--back" aria-label="Business card back">
    <div class="brand">
      <span class="brand-name">Clinicians Keystone</span>
      <span class="brand-square" aria-hidden="true"></span>
    </div>
    <p class="web">www.cliniciankeystone.com</p>
  </section>

</body>
</html>
```